Copperleaf Roofing Business Card

This is my current business card. But I’d like to make some changes. Somewhere on the card I’d like to list some of the services we offer. Maybe on the back? But I’d still like to keep the red. White and black modern look.

-residential & commercial roofing
-Roof Repairs & Maintenance
-Storm Damage & Insurance Claims specialist
-Christmas Lights and permanent Christmas lights
Fencing. Windows. Gutters. Siding. Sheetrock, painting.

```html
<!DOCTYPE html>
<html lang="en">
<head>
<meta charset="utf-8">
<title>Copperleaf Roofing Business Card</title>
<link rel="stylesheet" href="https://fonts.googleapis.com/css2?family=Montserrat:wght@500;700;800&family=Lato:wght@400&family=Oswald:wght@400&display=swap">
<style>
  :root {
    --red: #e3161b;
    --ink: #141416;
    --card-black: #151518;
    --paper: #ffffff;
    --grey: #6d6d70;
    --faint: #eeeeef;
    --stage: #2a2b2e;
  }
  * { box-sizing: border-box; margin: 0; padding: 0; }
  html, body { width: 1200px; height: 952px; overflow: hidden; }
  body {
    background: var(--stage);
    display: flex;
    flex-direction: column;
    align-items: center;
    justify-content: center;
    gap: 56px;
  }
  .card {
    position: relative;
    width: 700px;
    height: 400px;
    overflow: hidden;
    box-shadow: 0 10px 30px rgba(0,0,0,.45);
  }
  .card--front { background: var(--paper); color: var(--ink); }
  .card--back  { background: var(--card-black); color: #fff; }

  .brand {
    position: absolute;
    display: flex;
    align-items: center;
    gap: 14px;
    z-index: 1;
  }
  .brand__dot {
    width: 64px; height: 64px; border-radius: 50%;
    background: var(--red);
    flex: none;
  }
  .brand__name {
    font-family: "Montserrat", sans-serif;
    font-weight: 800;
    color: var(--red);
    font-size: 24px;
    line-height: 1.1;
    letter-spacing: 1px;
    text-transform: uppercase;
    white-space: nowrap;
  }
  .card--front .brand { left: 60px; top: 56px; }
  .card--back .brand { left: 70px; top: 70px; }
  .card--back .brand__dot { width: 76px; height: 76px; }

  .watermark {
    position: absolute;
    right: 150px; top: 150px;
    width: 330px; height: 330px;
    border-radius: 50%;
    background: var(--faint);
  }

  .contact {
    position: absolute;
    left: 60px; top: 205px;
    list-style: none;
    font-family: "Lato", sans-serif;
    font-size: 15px;
    color: var(--grey);
    z-index: 1;
  }
  .contact li { display: flex; align-items: center; gap: 12px; margin-bottom: 12px; }
  .contact svg { width: 20px; height: 20px; flex: none; }

  .person {
    position: absolute;
    right: 60px; top: 150px;
    text-align: right;
    z-index: 1;
  }
  .person__name {
    font-family: "Montserrat", sans-serif;
    font-weight: 700;
    font-size: 34px;
    letter-spacing: 2px;
    text-transform: uppercase;
  }
  .person__name .accent { color: var(--red); }
  .person__role {
    display: inline-block;
    margin-top: 4px;
    padding: 0 0 6px 40px;
    border-bottom: 2px solid var(--grey);
    font-family: "Montserrat", sans-serif;
    font-weight: 500;
    font-size: 20px;
    letter-spacing: 2px;
    color: var(--grey);
  }

  .services {
    position: absolute;
    left: 320px; top: 178px;
    list-style: none;
    font-family: "Oswald", sans-serif;
    font-size: 17px;
    line-height: 1.8;
  }
  .services li::before,
  .services .inline span::before {
    content: "•";
    color: var(--red);
    margin-right: 6px;
  }
  .services li.inline::before { content: none; }
  .services .inline { display: flex; gap: 18px; }
</style>
</head>
<body>
  <section class="card card--front" aria-label="Business card front">
    <div class="watermark" role="img" aria-label="Faint brand emblem decoration"></div>
    <div class="brand">
      <span class="brand__dot"></span>
      <span class="brand__name">Copperleaf<br>Roofing Co.</span>
    </div>
    <ul class="contact">
      <li>
        <svg viewBox="0 0 20 20"><rect width="20" height="20" rx="3" fill="#141416"/><path d="M6 4.5l2 .3.8 2.8-1.4 1a7 7 0 0 0 4 4l1-1.4 2.8.8.3 2c-.2.7-1 1-1.7 1A10 10 0 0 1 4.5 6.2c0-.7.3-1.5 1.5-1.7z" fill="#fff"/></svg>
        <span>555-014-2273</span>
      </li>
      <li>
        <svg viewBox="0 0 20 20"><rect width="20" height="20" rx="3" fill="#141416"/><rect x="4" y="6" width="12" height="8" fill="none" stroke="#fff" stroke-width="1.4"/><path d="M4 6l6 5 6-5" fill="none" stroke="#fff" stroke-width="1.4"/></svg>
        <span>daniel@copperleafroofing.co</span>
      </li>
      <li>
        <svg viewBox="0 0 20 20"><rect width="20" height="20" rx="3" fill="#141416"/><path d="M10 4a4 4 0 0 0-4 4c0 3 4 8 4 8s4-5 4-8a4 4 0 0 0-4-4z" fill="#fff"/><circle cx="10" cy="8" r="1.5" fill="#141416"/></svg>
        <span>www.copperleafroofing.co</span>
      </li>
    </ul>
    <div class="person">
      <h1 class="person__name">Daniel <span class="accent">Reeve</span></h1>
      <p class="person__role">OWNER</p>
    </div>
  </section>

  <section class="card card--back" aria-label="Business card back">
    <div class="brand">
      <span class="brand__dot"></span>
      <span class="brand__name">Copperleaf<br>Roofing Co.</span>
    </div>
    <ul class="services">
      <li>residential &amp; commercial roofing</li>
      <li>Roof Repairs &amp; Maintenance</li>
      <li>Storm Damage &amp; Insurance Claims specialist</li>
      <li>Christmas Lights and permanent Christmas lights</li>
      <li class="inline"><span>Fencing</span><span>Windows</span><span>Gutters</span><span>Siding</span></li>
      <li class="inline"><span>Sheetrock</span><span>painting</span></li>
    </ul>
  </section>
</body>
</html>
```